Corvane Card

The logo is the Spanish flag colors I want a vibrant eye catching design with the yellow / red colors over either Navy or white background or black even ,
Would like a 2D feel to the logo with another lighter color logo under it look ,

Contact Information for Business Card

Corvane Flooring
Teodor Vashkin
Main Number
Cell Number
Fax Number

Website on the side of the card somewhere

Font styles to use
Sans Serif

Colors
ec1f27
ffc214

Requirements
Must have
• 2 logos feel one is bolder and the other one underneath very light

```html
<!DOCTYPE html>
<html lang="en">
<head>
<meta charset="utf-8">
<title>Corvane Flooring – Business Card</title>
<link rel="stylesheet" href="https://fonts.googleapis.com/css2?family=Michroma&family=Arimo:wght@400&display=swap">
<style>
  :root {
    --brand-red: #ec1f27;
    --brand-yellow: #ffc214;
    --card-black: #0b0b0b;
    --stage: #1c1c1d;
    --ink-white: #ffffff;
    --ink-silver: #bfbfbf;
    --rule: #3a3a3a;
  }
  * { margin: 0; padding: 0; box-sizing: border-box; }
  html, body { width: 1200px; height: 900px; overflow: hidden; }
  body { background: var(--stage); position: relative; font-family: "Arimo", Arial, sans-serif; }

  .card {
    position: absolute;
    width: 620px; height: 354px;
    background: var(--card-black);
    border-radius: 26px;
  }
  .card--back { left: 520px; top: 70px; }
  .card--front { left: 80px; top: 460px; }

  /* Back face */
  .back-mark {
    position: absolute; inset: 0;
    display: flex; align-items: center; justify-content: center; gap: 16px;
  }
  .back-mark__square { width: 22px; height: 22px; background: var(--ink-silver); border-radius: 3px; }
  .back-mark__name {
    font-family: "Michroma", sans-serif;
    font-size: 24px; line-height: 1.3; letter-spacing: 2px;
    color: var(--ink-silver);
  }

  /* Front face */
  .front-mark {
    position: absolute; left: 40px; top: 0; bottom: 0; width: 220px;
    display: flex; flex-direction: column; justify-content: center; gap: 14px;
  }
  .front-mark__square { width: 26px; height: 26px; background: var(--brand-red); border-radius: 3px; }
  .front-mark__name {
    font-family: "Michroma", sans-serif;
    font-size: 22px; line-height: 1.35; letter-spacing: 1px;
    color: var(--brand-red);
  }
  .divider {
    position: absolute; left: 285px; top: 70px; bottom: 70px;
    width: 1px; background: var(--rule);
  }
  .contact { position: absolute; left: 315px; top: 88px; right: 20px; }
  .contact__name {
    font-family: "Michroma", sans-serif;
    font-size: 19px; letter-spacing: 1px; margin-bottom: 18px; white-space: nowrap;
  }
  .contact__first { color: var(--brand-red); }
  .contact__last { color: var(--brand-yellow); }
  .contact__list { list-style: none; }
  .contact__item {
    display: flex; align-items: center; gap: 12px;
    font-size: 16px; line-height: 27px; color: var(--ink-white);
  }
  .contact__icon { width: 15px; height: 15px; flex: none; }
  .contact__accent { color: var(--brand-red); }
</style>
</head>
<body>

<section class="card card--back" aria-label="Card back">
  <div class="back-mark">
    <span class="back-mark__square"></span>
    <span class="back-mark__name">CORVANE<br>FLOORING</span>
  </div>
</section>

<section class="card card--front" aria-label="Card front">
  <div class="front-mark">
    <span class="front-mark__square"></span>
    <span class="front-mark__name">CORVANE<br>FLOORING</span>
  </div>

  <div class="divider"></div>

  <div class="contact">
    <h1 class="contact__name"><span class="contact__first">TEODOR</span> <span class="contact__last">VASHKIN</span></h1>
    <ul class="contact__list">
      <li class="contact__item">
        <svg class="contact__icon" viewBox="0 0 16 16" aria-hidden="true"><path fill="#ec1f27" d="M2 5c0-2 3-3 6-3s6 1 6 3v1h-3V5H5v1H2zM4 7h8l2 7H2z"/></svg>
        444 555 2190
      </li>
      <li class="contact__item">
        <svg class="contact__icon" viewBox="0 0 16 16" aria-hidden="true"><rect x="4" y="1" width="8" height="14" rx="1.5" fill="none" stroke="#ec1f27" stroke-width="2"/></svg>
        888 555 7316
      </li>
      <li class="contact__item">
        <svg class="contact__icon" viewBox="0 0 16 16" aria-hidden="true"><path fill="#ec1f27" d="M4 1h8v4H4zM1 6h14v6h-3v3H4v-3H1zm5 5v2h4v-2z"/></svg>
        888 444 5820
      </li>
      <li class="contact__item">
        <svg class="contact__icon" viewBox="0 0 16 16" aria-hidden="true"><rect x="1" y="3" width="14" height="10" fill="#ec1f27"/><path d="M1 3l7 6 7-6" fill="none" stroke="#0b0b0b" stroke-width="1.4"/></svg>
        info@corvaneflooring.com
      </li>
      <li class="contact__item">
        <svg class="contact__icon" viewBox="0 0 16 16" aria-hidden="true"><circle cx="8" cy="8" r="7" fill="#ec1f27"/><path d="M1 8h14M8 1c-3 3-3 11 0 14M8 1c3 3 3 11 0 14" fill="none" stroke="#0b0b0b" stroke-width="1"/></svg>
        <span>www.<span class="contact__accent">corvaneflooring</span>.com</span>
      </li>
    </ul>
  </div>
</section>

</body>
</html>
```